Powerpoint and Word template required

We need PowerPoint and Word templates for all of our company branded materials and stationary. We have recently rebranded our website and would like something that is reflective of our new corporate branding. A sample of some of the documents we have created recently are attached and our website is below

http://lorwynmedical.com.au/

The word template will be used for all letters we send to clients and customers and we think we want the logo and ISO 9001 cert to only appear on the first page.

The powerpoint template has to be flexible as we use this for both marketing and training purposes. I have attached a couple of samples of the types of documents we create and note that these are very basic / crude and we would be looking for something that is a significant improvement on these

In the powerpoint template it would be good to have lots of standard layouts within the template, e.g. different 'standard layouts for multiple elements on a page including pictures and text etc.
Updates

Project Deadline Extended
Reason: Still looking for a professional yet modern template and important to us that we can see more tan just a title slide and the layout of the other slide master slides is very important to us. Many thanks, Dale

Industry/Entity Type

Healthcare

Font styles to use
Sans Serif

Colors
33a6d7

Requirements
Must have
• Templates must be versatile for use; powerpoint template must be able to be used for training materials and weel as marketing / pitch books.
• Word template must be able to be used as a basis for our corporate letter head through to RFP response type documents as well as Reference / Operating manual type of documents
• In terms of the design it must be consistent with our new corporate image which is best represented by our new website design; www.lorwynmedical.com

```html
<!DOCTYPE html>
<html lang="en">
<head>
<meta charset="utf-8">
<title>Lorwyn Medical – Presentation Template Layouts</title>
<link href="https://fonts.googleapis.com/css2?family=Open+Sans:wght@400;600;700&display=swap" rel="stylesheet">
<style>
:root{
  --canvas:#a3a3a3;
  --paper:#ffffff;
  --brand:#1b6fc2;
  --brand-dark:#1459a3;
  --brand-light:#33a6d7;
  --ink:#333333;
  --muted:#666666;
  --photo-a:#d9dee4;
  --photo-b:#eef1f4;
}
*{box-sizing:border-box;margin:0;padding:0}
html,body{width:848px;height:1200px;overflow:hidden}
body{background:var(--canvas);font-family:"Open Sans",Arial,sans-serif;color:var(--ink);position:relative}
.slide{position:absolute;background:var(--paper);overflow:hidden}
.logo{position:absolute;display:flex;align-items:center;gap:3px;color:var(--brand);font-weight:600;font-size:13px;line-height:1}
.logo-mark{width:11px;height:11px;background:var(--brand)}
.heading{position:absolute;left:22px;top:20px}
.heading h2{font-size:10px;font-weight:700;color:var(--brand)}
.heading p{font-size:8.5px;color:var(--ink);margin-top:3px}
.site{position:absolute;left:12px;bottom:8px;font-size:5.5px;color:var(--ink)}
.photo{position:absolute;background:linear-gradient(135deg,var(--photo-a),var(--photo-b))}
.small-title{font-size:6px;font-weight:700;color:var(--brand)}
.small-text{font-size:5.3px;line-height:1.45;color:var(--ink)}
.body-copy{position:absolute;font-size:5.3px;line-height:1.42;text-align:justify;color:var(--ink)}

/* cover */
.cover{left:26px;top:20px;width:372px;height:280px}
.cover .photo{left:0;top:0;width:372px;height:200px;background:linear-gradient(120deg,#e9e4de 0%,#dfe6ee 45%,#c9d6e4 100%)}
.cover .rule{position:absolute;left:0;top:200px;width:372px;height:4px;background:var(--brand-light)}
.cover .date{position:absolute;right:22px;top:55px;font-size:5.5px;color:var(--muted)}
.cover .client{position:absolute;left:32px;top:212px;font-size:11px;color:var(--brand-light)}
.cover .doc-title{position:absolute;left:32px;top:227px;font-size:8.5px;line-height:1.45;color:var(--ink)}
.cover .cert{position:absolute;left:343px;top:230px;width:16px;height:32px;background:#e4e4e4;border-top:6px solid #c0392b}
.cover .site{left:auto;right:24px}

/* numbered list */
.list{left:415px;top:18px;width:378px;height:282px}
.list-row{position:absolute;left:34px;display:flex;gap:10px;align-items:flex-start}
.tab{width:40px;height:23px;background:var(--brand);color:#fff;font-size:7.5px;display:flex;align-items:center;justify-content:center;border-radius:2px 11px 11px 2px}
.list-row .small-text{width:270px}

/* text + photo */
.article{left:26px;top:310px;width:374px;height:280px}

/* icon grid */
.grid{left:418px;top:308px;width:384px;height:288px}
.grid-item{position:absolute;width:110px}
.grid-item .head{display:flex;align-items:center;gap:4px;margin-bottom:6px}
.icon-dot{width:20px;height:20px;border-radius:50%;background:var(--brand);color:#fff;font-size:6px;display:flex;align-items:center;justify-content:center}

/* process */
.process{left:26px;top:601px;width:378px;height:283px}
.step{position:absolute;top:72px;width:88px}
.step svg{display:block}
.step ul{list-style:none;margin-top:10px}
.step li{font-size:5.3px;line-height:2.1;color:var(--ink)}
.step li::before{content:"➢ ";}

/* product feature */
.feature{left:420px;top:612px;width:384px;height:284px;background:var(--brand)}
.feature .band{position:absolute;left:0;top:0;width:384px;height:28px;background:var(--paper)}
.feature .frame{position:absolute;left:16px;top:10px;width:148px;height:130px;background:var(--paper);padding:6px}
.feature .frame .photo{position:static;width:100%;height:100%;background:linear-gradient(160deg,#4aa39a,#d7dbde)}
.feature .body-copy{color:#fff;left:24px;top:158px;width:152px}
.feature-list{position:absolute;left:192px;top:54px;width:172px}
.feature-list div{margin-bottom:9px;color:#fff}
.feature-list .small-title{color:#fff}
.feature-list .small-text{color:#fff}

/* stairs */
.stairs{left:26px;top:900px;width:376px;height:282px}
.stair-row{position:absolute;left:140px;display:flex;gap:8px;align-items:flex-start}
.stair-row .tab{width:30px;height:20px;border-radius:0;background:var(--brand-light)}
.stair-row .small-text{width:160px}
</style>
</head>
<body>

<!-- Cover -->
<section class="slide cover">
  <div class="photo" role="img" aria-label="Photo of a smiling doctor with a stethoscope in a bright hospital ward"></div>
  <div class="logo" style="right:22px;top:22px"><span class="logo-mark"></span>Lorwyn</div>
  <div class="date">March 2016</div>
  <div class="rule"></div>
  <div class="client">EASTVALE HEALTH</div>
  <div class="doc-title">REVIEW OF PRESSURE INJURY<br>PREVENTION EQUIPMENT</div>
  <div class="cert" role="img" aria-label="Quality certification badge"></div>
  <div class="site">www.lorwynmedical.com</div>
</section>

<!-- Numbered list -->
<section class="slide list">
  <div class="heading" style="left:34px"><h2>Insert your Sub heading here</h2><p>Your sub title here</p></div>
  <div class="logo" style="right:20px;top:12px"><span class="logo-mark"></span>Lorwyn</div>
  <div class="list-row" style="top:64px"><div class="tab">01</div><div><div class="small-title">Insert your text here</div><div class="small-text">What we need is a template (or master) which can be varied by ourselves from case to case. Most of our cases are colorful and it´s important to transport the passion of</div></div></div>
  <div class="list-row" style="top:102px"><div class="tab">02</div><div><div class="small-title">Insert your text here</div><div class="small-text">What we need is a template (or master) which can be varied by ourselves from case to case. Most of our cases are colorful and it´s important to transport the passion of</div></div></div>
  <div class="list-row" style="top:140px"><div class="tab">03</div><div><div class="small-title">Insert your text here</div><div class="small-text">What we need is a template (or master) which can be varied by ourselves from case to case. Most of our cases are colorful and it´s important to transport the passion of</div></div></div>
  <div class="list-row" style="top:178px"><div class="tab">04</div><div><div class="small-title">Insert your text here</div><div class="small-text">What we need is a template (or master) which can be varied by ourselves from case to case. Most of our cases are colorful and it´s important to transport the passion of</div></div></div>
  <div class="list-row" style="top:216px"><div class="tab">05</div><div><div class="small-title">Insert your text here</div><div class="small-text">What we need is a template (or master) which can be varied by ourselves from case to case. Most of our cases are colorful and it´s important to transport the passion of</div></div></div>
  <div class="site">www.lorwynmedical.com</div>
</section>

<!-- Text with photo -->
<section class="slide article">
  <div class="heading" style="left:34px"><h2>Insert your Sub heading here</h2><p>Your sub title here</p></div>
  <div class="logo" style="right:20px;top:12px"><span class="logo-mark"></span>Lorwyn</div>
  <div class="photo" style="left:38px;top:48px;width:144px;height:106px;background:linear-gradient(135deg,#9bc3de,#e3e9ef)" role="img" aria-label="Photo of a nurse caring for an elderly patient in bed"></div>
  <div class="body-copy" style="left:38px;top:160px;width:146px">materially from those described in the statements. These risks and uncertainties include, but are not limited to, the following: the uncertainty of our ability to achieve expected levels of comparable restaurant sales increases due to factors such as decreased consumer spending and economic uncertainty or our failure to attract customers to our brand or retain our existing customers; our possible inability to increase menu prices or realize the benefits of menu price increases, or the impact of competition; factors that could affect our ability to achieve and manage our planned</div>
  <div class="body-copy" style="left:200px;top:52px;width:150px">expansion, such as the availability of a sufficient number of suitable new restaurant sites and the availability of qualified employees; the performance of new restaurants and their impact on existing restaurant sales; increases in the cost of food ingredients and other key supplies; the potential for increased labor costs or difficulty retaining qualified employees, including as a result of immigration enforcement activities; security risks associated with the acceptance of electronic payment cards or electronic storage of confidential customer or employee information; the risk of food-borne illnesses and other health concerns about our food; risks relating to our expansion into international markets; the impact of federal, state or local government regulations relating to our employees, our restaurant design, or the sale of food or alcoholic beverages; risks associated with supply shortages; the effect of competition in the restaurant industry; risks relating to litigation and negative publicity; risks that our investments in new concepts will not be successful; risks related to our marketing and advertising strategies; our dependence on key personnel; risks relating to our insurance coverage; the uncertainty of our ability to protect our name, logo and other proprietary information or the reputation of our brand; the potential effects of inclement weather; and other risk factors described from time to time in our communications.</div>
  <div class="site">www.lorwynmedical.com</div>
</section>

<!-- Icon grid -->
<section class="slide grid">
  <div class="heading" style="left:34px"><h2>Insert your Sub heading here</h2><p>Your sub title here</p></div>
  <div class="logo" style="right:20px;top:12px"><span class="logo-mark"></span>Lorwyn</div>
  <div class="grid-item" style="left:34px;top:64px"><div class="head"><span class="icon-dot">icon</span><span class="small-title">Insert your text here</span></div><div class="small-text">What we need is a template (or master) which can be varied by ourselves from case to case. Most of our cases are colorful and it´s important to transport the passion</div></div>
  <div class="grid-item" style="left:146px;top:64px"><div class="head"><span class="icon-dot">icon</span><span class="small-title">Insert your text here</span></div><div class="small-text">What we need is a template (or master) which can be varied by ourselves from case to case. Most of our cases are colorful and it´s important to transport the passion of</div></div>
  <div class="grid-item" style="left:260px;top:64px"><div class="head"><span class="icon-dot">icon</span><span class="small-title">Insert your text here</span></div><div class="small-text">What we need is a template (or master) which can be varied by ourselves from case to case. Most of our cases are colorful and it´s important to transport the passion</div></div>
  <div class="grid-item" style="left:34px;top:150px"><div class="head"><span class="icon-dot">icon</span><span class="small-title">Insert your text here</span></div><div class="small-text">What we need is a template (or master) which can be varied by ourselves from case to case. Most of our cases are colorful and it´s important to transport the passion</div></div>
  <div class="grid-item" style="left:146px;top:150px"><div class="head"><span class="icon-dot">icon</span><span class="small-title">Insert your text here</span></div><div class="small-text">What we need is a template (or master) which can be varied by ourselves from case to case. Most of our cases are colorful and it´s important to transport the passion of</div></div>
  <div class="grid-item" style="left:260px;top:150px"><div class="head"><span class="icon-dot">icon</span><span class="small-title">Insert your text here</span></div><div class="small-text">What we need is a template (or master) which can be varied by ourselves from case to case. Most of our cases are colorful and it´s important to transport the passion</div></div>
  <div class="site">www.lorwynmedical.com</div>
</section>

<!-- Process -->
<section class="slide process">
  <div class="heading" style="left:34px"><h2>Insert your Sub heading here</h2><p>Your sub title here</p></div>
  <div class="logo" style="right:20px;top:12px"><span class="logo-mark"></span>Lorwyn</div>
  <div class="step" style="left:36px">
    <svg width="86" height="90" viewBox="0 0 86 90"><path d="M30 16 A27 27 0 1 0 30 70 L56 70 L74 43 L56 16 Z" fill="var(--brand)"/><circle cx="6" cy="14" r="6" fill="#fff" stroke="#888" stroke-width=".6"/><text x="6" y="16.5" font-size="7" text-anchor="middle" fill="#333">1</text><path d="M25 28 h4 l5 -3 v8 l-5 -3 h-4z" fill="#fff"/><text x="30" y="47" font-size="6" fill="#fff" text-anchor="middle">Your text</text><text x="30" y="55" font-size="6" fill="#fff" text-anchor="middle">here</text><line x1="30" y1="72" x2="30" y2="88" stroke="#aaa" stroke-width=".6"/></svg>
    <ul><li>Digital, interactive, networ</li><li>user-generated content.</li><li>networks determine our</li><li>lives. This includes blogs,</li><li>micro blogs, and social</li><li>networks like</li></ul>
  </div>
  <div class="step" style="left:120px">
    <svg width="86" height="90" viewBox="0 0 86 90"><path d="M30 16 A27 27 0 1 0 30 70 L56 70 L74 43 L56 16 Z" fill="var(--brand)"/><circle cx="6" cy="14" r="6" fill="#fff" stroke="#888" stroke-width=".6"/><text x="6" y="16.5" font-size="7" text-anchor="middle" fill="#333">2</text><circle cx="27" cy="26" r="2" fill="#fff"/><circle cx="33" cy="26" r="2" fill="#fff"/><rect x="25" y="29" width="4" height="5" fill="#fff"/><rect x="31" y="29" width="4" height="5" fill="#fff"/><text x="30" y="47" font-size="6" fill="#fff" text-anchor="middle">Your text</text><text x="30" y="55" font-size="6" fill="#fff" text-anchor="middle">here</text><line x1="30" y1="72" x2="30" y2="88" stroke="#aaa" stroke-width=".6"/></svg>
    <ul><li>Digital, interactive,</li><li>networuser-generated</li><li>content.</li><li>networks determine our</li><li>lives. This includes blogs,</li><li>micro blogs, and social</li><li>networks like</li></ul>
  </div>
  <div class="step" style="left:204px">
    <svg width="86" height="90" viewBox="0 0 86 90"><path d="M30 16 A27 27 0 1 0 30 70 L56 70 L74 43 L56 16 Z" fill="var(--brand)"/><circle cx="6" cy="14" r="6" fill="#fff" stroke="#888" stroke-width=".6"/><text x="6" y="16.5" font-size="7" text-anchor="middle" fill="#333">3</text><path d="M25 27 h10 l-2 -2 M35 32 h-10 l2 2" stroke="#fff" fill="none" stroke-width="1.2"/><text x="30" y="47" font-size="6" fill="#fff" text-anchor="middle">Your text</text><text x="30" y="55" font-size="6" fill="#fff" text-anchor="middle">here</text><line x1="30" y1="72" x2="30" y2="88" stroke="#aaa" stroke-width=".6"/></svg>
    <ul><li>Digital, interactive, networ</li><li>user-generated content.</li><li>networks determine our</li><li>lives. This includes blogs,</li><li>micro blogs, and social</li><li>networks like</li></ul>
  </div>
  <div class="step" style="left:288px">
    <svg width="86" height="90" viewBox="0 0 86 90"><path d="M30 16 A27 27 0 1 0 30 70 L56 70 L74 43 L56 16 Z" fill="var(--brand)"/><circle cx="6" cy="14" r="6" fill="#fff" stroke="#888" stroke-width=".6"/><text x="6" y="16.5" font-size="7" text-anchor="middle" fill="#333">4</text><rect x="25" y="30" width="2" height="4" fill="#fff"/><rect x="29" y="28" width="2" height="6" fill="#fff"/><rect x="33" y="26" width="2" height="8" fill="#fff"/><text x="30" y="52" font-size="6" fill="#fff" text-anchor="middle">Your text</text><text x="30" y="60" font-size="6" fill="#fff" text-anchor="middle">here</text><line x1="30" y1="72" x2="30" y2="88" stroke="#aaa" stroke-width=".6"/></svg>
    <ul><li>Digital, interactive, networ</li><li>user-generated content.</li><li>networks determine our</li><li>lives. This includes blogs,</li><li>micro blogs, and social</li><li>networks like</li></ul>
  </div>
  <div class="site">www.lorwynmedical.com</div>
</section>

<!-- Product feature -->
<section class="slide feature">
  <div class="band"></div>
  <div class="logo" style="right:20px;top:10px"><span class="logo-mark"></span>Lorwyn</div>
  <div class="frame"><div class="photo" role="img" aria-label="Photo of a hospital bed with a pressure-relief air mattress"></div></div>
  <div class="body-copy">materially from those described in the statements. These risks and uncertainties include, but are not limited to, the following: the uncertainty of our ability to achieve expected levels of comparable restaurant sales increases due to factors such as decreased consumer spending and economic uncertainty or our failure to attract customers to our brand or retain our existing customers; our possible inability to increase menu prices or realize the benefits of menu price increases, or the impact of competition; factors that could affect our ability to achieve and manage our planeed</div>
  <div class="feature-list">
    <div><div class="small-title">Insert your text here</div><div class="small-text">What we need is a template (or master) which can be varied by ourselves from case to case. Most of our cases are colorful and it´s important to transport the passion of</div></div>
    <div><div class="small-title">Insert your text here</div><div class="small-text">What we need is a template (or master) which can be varied by ourselves from case to case. Most of our cases are colorful and it´s important to transport the passion of</div></div>
    <div><div class="small-title">Insert your text here</div><div class="small-text">What we need is a template (or master) which can be varied by ourselves from case to case. Most of our cases are colorful and it´s important to transport the passion of</div></div>
    <div><div class="small-title">Insert your text here</div><div class="small-text">What we need is a template (or master) which can be varied by ourselves from case to case. Most of our cases are colorful and it´s important to transport the passion of</div></div>
    <div><div class="small-title">Insert your text here</div><div class="small-text">What we need is a template (or master) which can be varied by ourselves from case to case. Most of our cases are colorful and it´s important to transport the passion of</div></div>
  </div>
</section>

<!-- Stairs -->
<section class="slide stairs">
  <div class="heading" style="left:34px"><h2>Insert your Sub heading here</h2><p>Your sub title here</p></div>
  <div class="logo" style="right:20px;top:12px"><span class="logo-mark"></span>Lorwyn</div>
  <svg style="position:absolute;left:28px;top:58px" width="120" height="160" viewBox="0 0 120 160">
    <path d="M84 0 L112 0 L90 20 L62 20 Z" fill="var(--brand-light)"/>
    <path d="M62 20 L90 20 L54 58 L26 58 Z" fill="var(--brand)"/>
    <path d="M84 36 L112 36 L90 58 L62 58 Z" fill="var(--brand-light)"/>
    <path d="M84 72 L112 72 L90 94 L62 94 Z" fill="var(--brand-light)"/>
    <path d="M84 108 L112 108 L90 130 L62 130 Z" fill="var(--brand-light)"/>
    <path d="M26 58 L62 58 L62 94 L38 120 L38 154 L74 154 L90 130 L62 130 L90 94 L62 94 L90 58 L54 58 Z" fill="var(--brand-dark)"/>
    <path d="M26 58 L54 58 L54 154 L38 154 L38 120 L26 110 Z" fill="var(--brand)"/>
  </svg>
  <div class="stair-row" style="top:62px"><div class="tab">01</div><div><div class="small-title">Insert your text here</div><div class="small-text">What we need is a template (or master) which can be varied by ourselves from case to case. Most of our cases are colorful</div></div></div>
  <div class="stair-row" style="top:97px"><div class="tab">02</div><div><div class="small-title">Insert your text here</div><div class="small-text">What we need is a template (or master) which can be varied by ourselves from case to case. Most of our cases are colorful</div></div></div>
  <div class="stair-row" style="top:133px"><div class="tab">03</div><div><div class="small-title">Insert your text here</div><div class="small-text">What we need is a template (or master) which can be varied by ourselves from case to case. Most of our cases are colorful</div></div></div>
  <div class="stair-row" style="top:170px"><div class="tab">04</div><div><div class="small-title">Insert your text here</div><div class="small-text">What we need is a template (or master) which can be varied by ourselves from case to case. Most of our cases are colorful</div></div></div>
  <div class="site">www.lorwynmedical.com</div>
</section>

</body>
</html>
```